Pine leaf & Snapvista ad needed

I am in need of a simple static image ad to be used for Pineleaf & Snapvista. A photo of a nice roof on a nice house. "Instant Satellite Roof Estimates" "Your house, your time & instant estimate" . Our logo file is here: https://www.filecrate-example.net/share/q73kdm41xv9wpz2tbn8hs/JKsT4mWQpZ2xYcVn8bRfL6d?key=wm5tz81qvjx3c7bnd0ke9fa4r&v=0

Multiple variations will be purchased.

```html
<!DOCTYPE html>
<html lang="en">
<head>
<meta charset="UTF-8">
<title>Crestline Roofing – Instant Satellite Roof Estimates</title>
<link href="https://fonts.googleapis.com/css2?family=Saira:wdth,wght@100..125,400..700&display=swap" rel="stylesheet">
<style>
  :root {
    --ink: #000000;
    --paper: #ffffff;
    --sky: #a9c1d8;
    --pine: #3f5a30;
    --foliage: #7a6a3a;
    --roof: #6b6d70;
    --siding: #c8ccd0;
    --lawn: #4e9a2a;
    --lawn-deep: #3c7f1f;
  }
  * { margin: 0; padding: 0; box-sizing: border-box; }
  html, body { width: 1200px; height: 1200px; overflow: hidden; background: var(--paper); }
  .ad {
    position: relative;
    width: 1200px;
    height: 1200px;
    background: var(--paper);
    font-family: "Saira", "Arial", sans-serif;
    color: var(--ink);
    overflow: hidden;
  }
  .brand {
    position: absolute;
    left: 63px;
    top: 70px;
    color: var(--ink);
    line-height: 1;
    font-weight: 500;
  }
  .brand-name { display: block; font-size: 56px; letter-spacing: 0.5px; }
  .brand-sub { display: block; font-size: 21px; letter-spacing: 4px; margin-top: 4px; text-align: right; }
  .cta {
    position: absolute;
    left: 742px;
    top: 37px;
    width: 389px;
    height: 93px;
    background: var(--ink);
    color: var(--paper);
    border-radius: 8px;
    display: flex;
    align-items: center;
    justify-content: center;
    font-size: 31px;
    font-weight: 500;
    font-stretch: 108%;
  }
  .hero-photo {
    position: absolute;
    left: 0;
    top: 178px;
    width: 1200px;
    height: 740px;
    background:
      radial-gradient(ellipse 38% 22% at 30% 28%, rgba(107,109,112,0.85), rgba(107,109,112,0) 100%),
      radial-gradient(ellipse 30% 18% at 72% 40%, rgba(107,109,112,0.8), rgba(107,109,112,0) 100%),
      radial-gradient(ellipse 55% 22% at 48% 58%, rgba(200,204,208,0.95), rgba(200,204,208,0) 100%),
      radial-gradient(ellipse 22% 30% at 92% 30%, rgba(122,106,58,0.7), rgba(122,106,58,0) 100%),
      linear-gradient(180deg, var(--sky) 0%, var(--pine) 14%, #5b6b45 30%, var(--siding) 52%, #9a9d96 66%, var(--lawn) 76%, var(--lawn-deep) 100%);
  }
  .roof-divider {
    position: absolute;
    left: 0;
    top: 0;
    width: 1200px;
    height: 1200px;
  }
  .headline {
    position: absolute;
    left: 0;
    width: 1148px;
    text-align: center;
    font-weight: 700;
    font-stretch: 105%;
    font-size: 92px;
    line-height: 1;
  }
  .headline-1 { top: 916px; }
  .headline-2 { top: 1021px; }
  .tagline {
    position: absolute;
    left: 0;
    top: 1121px;
    width: 1168px;
    text-align: center;
    font-weight: 600;
    font-stretch: 108%;
    font-size: 51px;
    line-height: 1;
  }
</style>
</head>
<body>
  <main class="ad">
    <div class="brand" aria-label="Crestline Roofing">
      <span class="brand-name">CRESTLINE</span>
      <span class="brand-sub">ROOFING</span>
    </div>
    <div class="cta">Get Free Estimates</div>

    <div class="hero-photo" role="img" aria-label="Photo of a two-storey white colonial house with a grey shingle roof, wraparound front porch, green lawn and autumn trees"></div>

    <svg class="roof-divider" viewBox="0 0 1200 1200" xmlns="http://www.w3.org/2000/svg" aria-hidden="true">
      <polygon points="0,904 600,795 1200,906 1200,1200 0,1200" fill="#000000"/>
      <polygon points="0,912 600,816 1200,922 1200,1200 0,1200" fill="#ffffff"/>
    </svg>

    <h1 class="headline headline-1">Instant Satellite Roof</h1>
    <p class="headline headline-2">Estimates</p>
    <p class="tagline">Your House, Your Time &amp; Instant Estimate</p>
  </main>
</body>
</html>
```